Business Card Design - Service Company

Use of the card mainly in living rooms and relations b2b We wish a card with a modern design, blue tones in the background would be a plus The card must be front / back (one side with the logo / the other with the information of contact )

Font styles to use
Serif

Requirements
Must have
• Using the map on the back of the business card Editable format! Photoshop CS2 / Illustrator CS2
Nice to have
• Mivrel Data IT Plein Ouest Commercial Center, 20417 Biguglia 0491847352 Siret 41873306200018 APE 9511Z https://www.fb.com/boutiquetech.mivreldata www.mivrel-data.com

```html
<!DOCTYPE html>
<html lang="en">
<head>
<meta charset="UTF-8">
<title>Mivrel Data IT – Business Card</title>
<link rel="stylesheet" href="https://fonts.googleapis.com/css2?family=Roboto:wght@400;500;700&display=swap">
<style>
  :root {
    --page-bg: #161616;
    --card-top: #2a2a2a;
    --card-bottom: #1d1d1d;
    --brand-blue: #2b8bd6;
    --text-white: #f2f2f2;
    --text-grey: #9a9a9a;
  }
  html, body {
    margin: 0;
    padding: 0;
    width: 1200px;
    height: 900px;
    overflow: hidden;
    background: var(--page-bg);
    font-family: "Roboto", sans-serif;
  }
  .canvas {
    position: relative;
    width: 1200px;
    height: 900px;
  }
  .card {
    position: absolute;
    left: 270px;
    width: 660px;
    height: 377px;
    background: linear-gradient(160deg, var(--card-top), var(--card-bottom));
    box-shadow: 0 10px 30px rgba(0,0,0,0.6);
  }
  .card--front { top: 40px; }
  .card--back { top: 470px; }

  .wordmark {
    display: flex;
    align-items: center;
    gap: 12px;
    color: var(--brand-blue);
    font-weight: 700;
    white-space: nowrap;
  }
  .wordmark__square {
    width: 14px;
    height: 14px;
    background: var(--brand-blue);
  }

  .card--front .wordmark {
    position: absolute;
    top: 150px;
    left: 0;
    right: 0;
    justify-content: center;
    font-size: 48px;
  }
  .registration {
    position: absolute;
    bottom: 28px;
    left: 0;
    right: 0;
    text-align: center;
    color: var(--text-white);
    font-size: 17px;
    font-weight: 500;
    letter-spacing: 0.5px;
  }

  .card--back .wordmark {
    position: absolute;
    top: 165px;
    left: 38px;
    font-size: 30px;
  }
  .divider {
    position: absolute;
    left: 318px;
    top: 90px;
    width: 2px;
    height: 200px;
    background: var(--brand-blue);
  }
  .contact {
    position: absolute;
    left: 345px;
    top: 95px;
    color: var(--text-white);
  }
  .contact__name {
    margin: 0;
    color: var(--brand-blue);
    font-size: 28px;
    font-weight: 500;
    letter-spacing: 2px;
    text-transform: uppercase;
  }
  .contact__role {
    margin: 2px 0 16px;
    font-size: 17px;
    font-weight: 500;
  }
  .contact__address {
    margin: 0 0 12px;
    font-size: 17px;
    font-weight: 500;
    line-height: 1.35;
    font-style: normal;
  }
  .contact__line {
    display: flex;
    align-items: center;
    gap: 10px;
    font-size: 17px;
    font-weight: 500;
    margin-bottom: 5px;
  }
  .contact__icon {
    width: 13px;
    height: 13px;
    flex: none;
  }
  .contact__dot {
    width: 9px;
    height: 9px;
    margin: 0 2px;
    border-radius: 50%;
    background: var(--brand-blue);
    flex: none;
  }
</style>
</head>
<body>
<main class="canvas">

  <section class="card card--front" aria-label="Card front">
    <div class="wordmark">
      <span class="wordmark__square"></span>
      <span>Mivrel Data IT</span>
    </div>
    <p class="registration">Siret 41873306200018 APE 9511Z</p>
  </section>

  <section class="card card--back" aria-label="Card back">
    <div class="wordmark">
      <span class="wordmark__square"></span>
      <span>Mivrel Data IT</span>
    </div>
    <div class="divider"></div>
    <div class="contact">
      <h1 class="contact__name">Daniel Rouvier</h1>
      <p class="contact__role">Director</p>
      <address class="contact__address">Plein Ouest Commercial Center,<br>20417 Biguglia</address>
      <div class="contact__line">
        <svg class="contact__icon" viewBox="0 0 24 24" aria-hidden="true">
          <path fill="#2b8bd6" d="M6.6 10.8a15.1 15.1 0 0 0 6.6 6.6l2.2-2.2a1 1 0 0 1 1-.25 11.4 11.4 0 0 0 3.6.57 1 1 0 0 1 1 1V20a1 1 0 0 1-1 1A17 17 0 0 1 3 4a1 1 0 0 1 1-1h3.5a1 1 0 0 1 1 1c0 1.25.2 2.45.57 3.57a1 1 0 0 1-.25 1z"/>
        </svg>
        <span>0491847352</span>
      </div>
      <div class="contact__line">
        <svg class="contact__icon" viewBox="0 0 24 24" aria-hidden="true" fill="none" stroke="#2b8bd6" stroke-width="2">
          <circle cx="12" cy="12" r="10"/>
          <ellipse cx="12" cy="12" rx="4.5" ry="10"/>
          <line x1="2" y1="12" x2="22" y2="12"/>
        </svg>
        <span>www.mivrel-data.com</span>
      </div>
      <div class="contact__line">
        <span class="contact__dot"></span>
        <span>/boutiquetech.mivreldata</span>
      </div>
    </div>
  </section>

</main>
</body>
</html>
```